Redo our website for our Robotics company

We sell robotic equipment to the restaurant industry. Our current robot, is a cooking robot that cooks up to 15 lbs of food. We will provide a prior website as well as brand guidelines. We plan on using wordpress and take advantage of wordpress's visual (no code) editor.

Current website - https://kelvatrix88.com/ (please note we are only selling Tammo now and no longer selling Plavo+

We want someone to take our existing content and design the website as well as layout our content we provide. Here's a suggested site layout:

✅ KelvaTrix88 Website Wireframe / Site Map
1. Home

Purpose: Introduce Tammo, establish credibility, drive demo requests.

Sections:

Hero Section

Headline: “Meet Tammo — Your New Robotic Chef for High-Volume, Consistent Cooking.”

Sub-headline: Increase throughput. Reduce labor. Deliver perfect food every time.

CTA: Request a Demo + Watch Tammo Cook

Visual: Video loop or hero animation of Tammo in action.

How Tammo Works (3-4 steps)

Step cards: Load Ingredients → Select Recipe → Tammo Cooks → Serve

Icons and short explanations.

Key Benefits

Labor savings

Zero inconsistency

24/7 uptime

Throughput increases (30–50% faster)

Health & safety compliance

Who It’s For

QSR restaurants

Fast casual

Catering/commissaries

Ghost kitchens

Case Studies / Testimonials

Logo bar + quotes

“Tammo helped us reduce cooking times by 40%.”

Video Section

“Watch Tammo cook a full batch from start to finish.”

CTA Section

Big banner: Book a Demo

2. Product: “Meet Tammo”

Purpose: Deep dive into hardware, software, safety, reliability.

Sections:

Overview

What Tammo is

What tasks it automates

Where it fits in a kitchen

Hardware Features

High-temperature cooking chamber

Precision sensors

Automated stirring

Automated dispensing

Safety mechanisms (locking lids, auto-shutoff)

Software & AI

Recipe automation

IoT dashboard

Remote monitoring

Predictive maintenance

Specs Table

Dimensions

Power requirements

Capacity (lbs per batch)

Safety certifications

Gallery

Close-ups, installation photos, process shots

CTA: Request a Demo

3. Solutions

Purpose: Show that Tammo solves real operational problems.

Sub-pages or sections:

For Quick-Service Restaurants

Reduce labor cost

Speed up peak-hour demand

For Catering & Commissaries

Large-batch consistency

Automate repetitive cooking tasks

For High-Growth Chains

Replicable quality across multiple locations

Centralized recipe control

Each solution page includes:

A problem statement

How Tammo solves it

Metrics / KPIs

Relevant testimonial

CTA

4. ROI / Economics

Purpose: Sell the financial story clearly.

Sections:

Savings Calculator

Labor hours saved

Cost savings

Throughput increases

Food waste reduction

Before & After Comparison

Traditional kitchen vs. robotic kitchen

Sample ROI

“Payback in as little as 3–6 months.”

Download Full ROI Report (PDF)

5. Case Studies

Purpose: Social proof + real results.

Structure for each case study:

Customer background

Problem

Implementation

KPIs achieved

Labor savings

Consistency improvements

Cooking speed

Quote + photos/video

6. Pricing

Purpose: Start a commercial conversation.

Include:

Subscription model (monthly / annual)

Hardware leasing or purchase options

Installation + training

Support level

CTA to book a sales call

7. About

Purpose: Build trust.

Sections:

Mission statement

Founding team

Advisors/partners

“Why we built Tammo”

8. Resources

Purpose: SEO + education.

Subpages:

Blog (e.g., “The Future of Automated Kitchens”)

Whitepapers

Technical documentation

Product videos

9. Contact

General inquiry form

Sales contact

Support portal

Careers

```html
<!DOCTYPE html>
<html lang="en">
<head>
<meta charset="utf-8">
<title>KelvaTrix88 — Meet Tammo</title>
<link rel="stylesheet" href="https://fonts.googleapis.com/css2?family=Outfit:wght@400;500;600&family=Tinos&display=swap">
<style>
:root{
  --navy:#0b2d5b;
  --navy-band:#0f3a6f;
  --navy-line:#24508a;
  --red:#ef3b32;
  --orange:#f2833c;
  --white:#ffffff;
  --muted:#dfe7f3;
  --star:#f5c23c;
}
*{margin:0;padding:0;box-sizing:border-box}
html,body{width:1200px;height:3293px;overflow:hidden}
body{background:var(--navy);color:var(--white);font-family:'Outfit',sans-serif;position:relative}
.abs{position:absolute}
.logo{font-family:'Outfit',sans-serif;font-weight:600;font-size:34px;color:var(--red);letter-spacing:-.5px;display:flex;align-items:center;gap:10px;left:50%;transform:translateX(-50%)}
.logo i{width:12px;height:12px;background:var(--orange);border-radius:50%;display:block}
.nav{left:112px;right:114px;top:92px;display:flex;justify-content:space-between;font-size:14px;font-weight:500}
.nav a{color:var(--white);text-decoration:none}
.nav a.active{color:var(--orange)}
.hero-media{left:140px;top:134px;width:924px;height:428px;border-radius:44px;transform:skewX(-5deg);background:linear-gradient(100deg,#141a22 0%,#2b333d 38%,#8e949b 62%,#c6cacd 80%,#6d737a 100%);overflow:hidden}
.hero-copy{left:183px;top:278px}
.hero-copy h1{font-size:25px;font-weight:500;color:var(--orange);line-height:42px}
.hero-copy p{font-size:16px;margin-top:22px}
.btn{display:inline-block;border-radius:22px;font-size:14px;font-weight:500;padding:0 22px;height:40px;line-height:40px;text-transform:uppercase}
.btn-red{background:var(--red);color:var(--white)}
.btn-ghost{border:1.5px solid var(--red);color:var(--red);margin-left:14px}
.hero-ctas{margin-top:34px}
.title{left:0;width:1200px;text-align:center;font-size:31px;font-weight:500}
.title span{color:var(--red)}
.rule{left:580px;width:40px;height:2px;background:var(--red)}
.step{width:260px;text-align:center}
.step .ring{width:114px;height:114px;border-radius:50%;border:1.5px solid var(--navy-line);margin:0 auto;background:#0d3262;position:relative;display:flex;align-items:center;justify-content:center}
.step .num{position:absolute;left:-2px;top:-4px;width:30px;height:30px;border-radius:50%;background:var(--red);font-size:12px;line-height:30px}
.step h3{font-family:'Tinos',serif;font-weight:400;font-size:18px;margin-top:27px}
.step p{font-size:15px;line-height:32px;margin-top:14px;color:var(--muted)}
.arrow{width:44px;height:2px;background:var(--white);top:794px}
.arrow::after{content:"";position:absolute;right:-2px;top:-3px;border-left:7px solid var(--white);border-top:4px solid transparent;border-bottom:4px solid transparent}
.band{left:0;top:1060px;width:1200px;height:717px;background:var(--navy-band)}
.benefit-photo{left:447px;top:1217px;width:307px;height:425px;border-radius:154px 154px 154px 154px/150px 150px 140px 140px;background:radial-gradient(ellipse at 50% 45%,#e8a57c 0%,#9a5a3e 35%,#51606c 62%,#a9c1cc 100%)}
.bicon{width:66px;height:66px;border-radius:50%;background:var(--red);border:3px solid #f86a5f;display:flex;align-items:center;justify-content:center}
.blabel{font-family:'Tinos',serif;font-size:18px;line-height:36px}
.card{width:230px;height:295px;border:1.5px solid var(--navy-line);border-radius:12px;background:#0d3264;top:1955px}
.card .ph{margin:10px;height:218px;border-radius:12px}
.card h4{font-family:'Tinos',serif;font-weight:400;font-size:15px;text-align:center;margin-top:26px}
.quote-name{left:340px;top:2395px;width:110px;text-align:center;font-size:20px;font-weight:600;line-height:24px}
.stars{left:499px;top:2336px;display:flex;gap:8px}
.quote{left:499px;top:2387px;font-size:16px}
.cite{left:499px;top:2437px;font-size:14px;text-transform:uppercase}
.dots{left:556px;top:2491px;display:flex;gap:16px}
.dots i{width:10px;height:10px;border-radius:50%;border:1.5px solid var(--red);display:block}
.dots i.on{background:var(--red)}
.video{left:140px;top:2588px;width:924px;height:409px;border-radius:44px;transform:skewX(5deg);background:linear-gradient(110deg,#6f6256 0%,#3c342d 40%,#231d19 70%,#1a1613 100%)}
.play{left:576px;top:2768px;width:46px;height:46px;border-radius:50%;background:var(--red);display:flex;align-items:center;justify-content:center}
.video-copy{left:679px;top:2720px}
.video-copy h2{font-size:24px;font-weight:500;line-height:42px}
.video-copy .btn{margin-top:22px;font-size:13px;height:38px;line-height:38px;padding:0 18px}
.foot-nav{left:136px;right:136px;top:3167px;display:flex;justify-content:space-between;font-size:14px;font-weight:500}
.copy{left:0;width:1200px;text-align:center;top:3221px;font-size:13px;font-weight:500}
</style>
</head>
<body>

<header>
  <div class="abs logo" style="top:26px"><i></i>KelvaTrix88</div>
  <nav class="abs nav">
    <a class="active" href="#">HOME</a><a href="#">PRODUCTS</a><a href="#">SOLUTIONS</a><a href="#">ROI / ECONOMICS</a><a href="#">CASE STUDIES</a><a href="#">PRICING</a><a href="#">ABOUT US</a><a href="#">RESOURCES</a><a href="#">CONTACT US</a>
  </nav>
</header>

<section class="hero">
  <div class="abs hero-media" role="img" aria-label="Row of Tammo cooking robots in a commercial kitchen"></div>
  <div class="abs hero-copy">
    <h1>Meet Tammo —<br>Your New Robotic Chef for<br>High-Volume, Consistent Cooking.</h1>
    <p>Increase throughput. Reduce labor. Deliver perfect food every time.</p>
    <div class="hero-ctas"><span class="btn btn-red">Request a Demo</span><span class="btn btn-ghost">Watch Tammo Cook</span></div>
  </div>
</section>

<section class="how">
  <h2 class="abs title" style="top:640px">How <span>Tammo Works</span></h2>
  <div class="abs rule" style="top:694px"></div>

  <div class="abs step" style="left:82px;top:738px">
    <div class="ring"><span class="num">01</span>
      <svg width="50" height="50" viewBox="0 0 50 50" fill="none" stroke="#fff" stroke-width="2"><path d="M8 26h34a17 14 0 0 1-34 0z"/><path d="M30 8l8 14" stroke="#ef3b32"/><circle cx="14" cy="14" r="3"/><circle cx="22" cy="18" r="2"/></svg></div>
    <h3>LOAD INGREDIENTS</h3><p>Staff loads raw ingredients<br>into Tammo.</p>
  </div>
  <div class="abs arrow" style="left:324px"></div>
  <div class="abs step" style="left:348px;top:738px">
    <div class="ring"><span class="num">02</span>
      <svg width="50" height="50" viewBox="0 0 50 50" fill="none" stroke="#fff" stroke-width="2"><rect x="12" y="6" width="26" height="36" rx="3"/><path d="M12 42v4h26" /><path d="M19 24h12v-6a5 5 0 0 0-12 0z" stroke="#ef3b32"/></svg></div>
    <h3>SELECT RECIPE</h3><p>Pre-programmed recipes<br>ensure consistent results.</p>
  </div>
  <div class="abs arrow" style="left:588px"></div>
  <div class="abs step" style="left:613px;top:738px">
    <div class="ring"><span class="num">03</span>
      <svg width="54" height="50" viewBox="0 0 54 50" fill="none" stroke="#fff" stroke-width="2"><rect x="20" y="6" width="14" height="12" rx="2" stroke="#ef3b32"/><path d="M8 30h38M10 30v12h34V30M6 46h42M14 20v10M40 20v10"/></svg></div>
    <h3>TAMMO COOKS</h3><p>Automated stirring, heating,<br>timing, safety monitoring.</p>
  </div>
  <div class="abs arrow" style="left:852px"></div>
  <div class="abs step" style="left:878px;top:738px">
    <div class="ring"><span class="num">04</span>
      <svg width="50" height="50" viewBox="0 0 50 50" fill="none" stroke="#fff" stroke-width="2"><path d="M10 30a15 15 0 0 1 30 0z"/><path d="M6 30h38M25 11v4M18 36l-6 8M32 36l6 8"/><path d="M6 10l2 2M44 10l-2 2" stroke="#ef3b32"/></svg></div>
    <h3>SERVE</h3><p>Batch finishes—perfect<br>every time.</p>
  </div>
</section>

<section>
  <div class="abs band"></div>
  <h2 class="abs title" style="top:1110px">Key <span>Benefits</span></h2>
  <div class="abs rule" style="top:1164px"></div>
  <div class="abs benefit-photo" role="img" aria-label="Stainless commercial kitchen with warm lighting"></div>

  <div class="abs bicon" style="left:414px;top:1286px"><svg width="32" height="32" viewBox="0 0 32 32" fill="none" stroke="#fff" stroke-width="2"><circle cx="16" cy="16" r="11"/><path d="M16 10v6l4 3"/></svg></div>
  <div class="abs bicon" style="left:717px;top:1276px"><svg width="32" height="32" viewBox="0 0 32 32" fill="none" stroke="#fff" stroke-width="2"><circle cx="13" cy="11" r="5"/><path d="M4 28a9 9 0 0 1 18 0"/><circle cx="24" cy="12" r="4"/></svg></div>
  <div class="abs bicon" style="left:414px;top:1497px"><svg width="32" height="32" viewBox="0 0 32 32" fill="none" stroke="#fff" stroke-width="2"><path d="M16 5l9 4v7c0 6-4 10-9 12-5-2-9-6-9-12V9z"/><path d="M16 11v9M11.5 15.5h9"/></svg></div>
  <div class="abs bicon" style="left:717px;top:1487px"><svg width="32" height="32" viewBox="0 0 32 32" fill="none" stroke="#fff" stroke-width="2"><rect x="8" y="6" width="16" height="21" rx="2"/><path d="M12 13h8M12 18h8M12 23h5"/></svg></div>
  <div class="abs bicon" style="left:566px;top:1602px"><svg width="32" height="32" viewBox="0 0 32 32" fill="none" stroke="#fff" stroke-width="2"><circle cx="16" cy="16" r="5"/><path d="M16 4v5M16 23v5M4 16h5M23 16h5M8 8l3 3M21 21l3 3M24 8l-3 3M8 24l3-3"/></svg></div>

  <div class="abs blabel" style="left:268px;top:1300px">24/7 UPTIME</div>
  <div class="abs blabel" style="left:815px;top:1291px">LABOR SAVINGS</div>
  <div class="abs blabel" style="left:217px;top:1493px;text-align:right;width:162px">HEALTH &amp; SAFETY<br>COMPLIANCE</div>
  <div class="abs blabel" style="left:815px;top:1502px">ZERO INCONSISTENCY</div>
  <div class="abs blabel" style="left:0;width:1200px;text-align:center;top:1691px">THROUGHPUT INCREASES (30–50% FASTER)</div>
</section>

<section>
  <h2 class="abs title" style="top:1855px">Who It’s <span>For</span></h2>
  <div class="abs rule" style="top:1910px"></div>
  <div class="abs card" style="left:111px"><div class="ph" role="img" aria-label="Quick-service restaurant counter" style="background:linear-gradient(180deg,#2a1c14,#b7692b 60%,#3a2418)"></div><h4>QSR RESTAURANTS</h4></div>
  <div class="abs card" style="left:360px"><div class="ph" role="img" aria-label="Fast casual service line" style="background:linear-gradient(180deg,#3a3633,#9a7a5c 60%,#5a3e2a)"></div><h4>FAST CASUAL</h4></div>
  <div class="abs card" style="left:609px"><div class="ph" role="img" aria-label="Catering spread on a long table" style="background:linear-gradient(160deg,#e9e2d8,#c79870 55%,#8d6a4c)"></div><h4>CATERING/COMMISSARIES</h4></div>
  <div class="abs card" style="left:858px"><div class="ph" role="img" aria-label="Ghost kitchen counter with seasonal decor" style="background:linear-gradient(180deg,#cfc7bd,#d8843a 60%,#e6e2dc)"></div><h4>GHOST KITCHENS</h4></div>
</section>

<section>
  <div class="abs quote-name">FENNEL<br>HOUSE</div>
  <div class="abs stars">
    <svg width="22" height="22" viewBox="0 0 24 24"><path fill="#f5c23c" d="M12 2l3 7 7 .6-5.3 4.7 1.6 7.2L12 17.8 5.7 21.5l1.6-7.2L2 9.6 9 9z"/></svg>
    <svg width="22" height="22" viewBox="0 0 24 24"><path fill="#f5c23c" d="M12 2l3 7 7 .6-5.3 4.7 1.6 7.2L12 17.8 5.7 21.5l1.6-7.2L2 9.6 9 9z"/></svg>
    <svg width="22" height="22" viewBox="0 0 24 24"><path fill="#f5c23c" d="M12 2l3 7 7 .6-5.3 4.7 1.6 7.2L12 17.8 5.7 21.5l1.6-7.2L2 9.6 9 9z"/></svg>
    <svg width="22" height="22" viewBox="0 0 24 24"><path fill="#f5c23c" d="M12 2l3 7 7 .6-5.3 4.7 1.6 7.2L12 17.8 5.7 21.5l1.6-7.2L2 9.6 9 9z"/></svg>
    <svg width="22" height="22" viewBox="0 0 24 24"><path fill="#f5c23c" d="M12 2l3 7 7 .6-5.3 4.7 1.6 7.2L12 17.8 5.7 21.5l1.6-7.2L2 9.6 9 9z"/></svg>
  </div>
  <p class="abs quote">Tammo helped us reduce cooking times by 40%.</p>
  <p class="abs cite">— Operations Director, Fast Casual Chain</p>
  <div class="abs dots"><i class="on"></i><i></i><i></i><i></i></div>
</section>

<section>
  <div class="abs video" role="img" aria-label="Chefs preparing a batch in a busy kitchen"></div>
  <div class="abs play"><svg width="16" height="16" viewBox="0 0 16 16"><path fill="#fff" d="M4 2l10 6-10 6z"/></svg></div>
  <div class="abs video-copy">
    <h2>Watch Tammo cook a full batch<br>from start to finish</h2>
    <span class="btn btn-red">Book a Demo</span>
  </div>
</section>

<footer>
  <div class="abs logo" style="top:3082px"><i></i>KelvaTrix88</div>
  <nav class="abs foot-nav"><span>HOME</span><span>PRODUCTS</span><span>SOLUTIONS</span><span>ROI / ECONOMICS</span><span>CASE STUDIES</span><span>PRICING</span><span>ABOUT</span><span>RESOURCES</span><span>CONTACT</span></nav>
  <p class="abs copy">©2025 COPYRIGHTS - ALL RIGHTS RESERVED</p>
</footer>

</body>
</html>
```